New Business Card for Web Design/Internet Marketing Company

Looking for a great looking new business card. We are a 10 year old web design, internet marketing and website management company that works mostly with small businesses.

Our new card needs to better match the colors and style of our website, be bold, extremely usable and slightly edgy.

Target Market(s)

Small/Medium businesses that have websites

Industry/Entity Type

Internet

Requirements
Must have
• Front and back design, full color, rounded corners please

Must use the colors/style of our website (JPG provided)

INFO FOR CARDS (as readable as possible please)
Mark Lenner
President/CEO
mark@trelvanmedia.example
Phone: 520-381-7459
Toll Free: 866-381-7459
Address: 4315 W. Calloway Ave. Ste. 140, Tucson, AZ 85792

THINGS I WANT TO PROMOTE (if there is room):
1. Our Website - www.trelvanmedia.example

2. Social Media
Twitter: @trelvanmedia
Facebook: www.facebook.com/trelvanmedia

3. Our Services
Web Design
Internet Marketing
Website Management

```html
<!DOCTYPE html>
<html lang="en">
<head>
<meta charset="utf-8">
<title>Trelvan Media – Business Card</title>
<link href="https://fonts.googleapis.com/css2?family=Ubuntu:wght@400;500;700&display=swap" rel="stylesheet">
<style>
  :root {
    --stage: #e9e6e2;
    --brand-blue: #0a8ec9;
    --brand-orange: #ef7d22;
    --card-white: #ffffff;
    --slate: #5b5c5e;
    --slate-faint: #6a6b6d;
    --text-light: #ffffff;
    --text-grey: #5b5c5e;
    --divider: #8d8e90;
  }
  * { box-sizing: border-box; margin: 0; padding: 0; }
  html, body { width: 1200px; height: 402px; overflow: hidden; }
  body {
    background: var(--stage);
    font-family: "Ubuntu", "Segoe UI", sans-serif;
    position: relative;
  }
  .card {
    position: absolute;
    top: 56px;
    width: 513px;
    height: 292px;
    overflow: hidden;
    box-shadow: 0 2px 6px rgba(0,0,0,0.25);
  }
  .card--front { left: 70px; background: var(--card-white); }
  .card--back { left: 617px; background: var(--slate); }

  /* Front */
  .name-band {
    height: 38px;
    background: var(--brand-blue);
    color: var(--text-light);
    text-align: center;
    line-height: 38px;
  }
  .name-band .person { font-weight: 700; font-size: 17px; }
  .name-band .title { font-size: 12px; margin-left: 3px; }

  .brand-area {
    height: 149px;
    display: flex;
    flex-direction: column;
    align-items: center;
    justify-content: center;
    gap: 2px;
    padding-top: 8px;
  }
  .brand-name {
    display: flex;
    align-items: center;
    gap: 14px;
    font-size: 52px;
    font-weight: 700;
    color: var(--brand-blue);
    letter-spacing: -0.5px;
    line-height: 1;
  }
  .brand-name .dot {
    width: 30px; height: 30px; border-radius: 50%;
    background: var(--brand-orange);
  }
  .tagline {
    align-self: flex-end;
    margin-right: 46px;
    font-size: 15px;
    color: var(--text-grey);
  }

  .contact-panel {
    position: absolute;
    left: 0; right: 0; bottom: 0;
    height: 105px;
    background: var(--slate);
    color: var(--text-light);
    font-size: 12.5px;
    line-height: 19px;
  }
  .contact-social {
    position: absolute;
    right: 266px;
    top: 13px;
    text-align: right;
  }
  .contact-social .gap { height: 8px; }
  .contact-divider {
    position: absolute;
    left: 263px; top: 14px;
    width: 1px; height: 78px;
    background: var(--divider);
  }
  .contact-direct {
    position: absolute;
    left: 276px;
    top: 13px;
  }
  .line { display: flex; align-items: center; gap: 4px; white-space: nowrap; }
  .contact-social .line { justify-content: flex-end; }
  .line svg { width: 10px; height: 10px; flex: none; }
  .social-square { width: 10px; height: 10px; background: var(--brand-blue); flex: none; }

  /* Back */
  .back-mark {
    position: absolute;
    left: 14px; top: 62px;
    width: 220px; height: 170px;
  }
  .back-name {
    position: absolute;
    left: 36px; top: 118px;
    font-size: 40px;
    font-weight: 700;
    color: var(--text-light);
  }
  .services {
    position: absolute;
    left: 272px; top: 117px;
    color: var(--text-light);
  }
  .services h2 { font-size: 23px; font-weight: 500; margin-bottom: 16px; }
  .services ul { list-style: none; font-size: 20px; line-height: 31px; }
</style>
</head>
<body>

<section class="card card--front">
  <header class="name-band">
    <span class="person">Mark Lenner,</span><span class="title">President/CEO</span>
  </header>

  <div class="brand-area">
    <div class="brand-name"><span class="dot"></span>trelvan media</div>
    <div class="tagline">Grow your Business</div>
  </div>

  <div class="contact-panel">
    <div class="contact-social">
      <div class="line"><span class="social-square"></span>trelvanmedia</div>
      <div class="line"><span class="social-square"></span>@trelvanmedia</div>
      <div class="gap"></div>
      <div class="line">4315 W. Calloway Ave. Ste. 140</div>
      <div class="line">Tucson, AZ 85792</div>
    </div>
    <div class="contact-divider"></div>
    <div class="contact-direct">
      <div class="line">
        <svg viewBox="0 0 10 10"><circle cx="5" cy="5" r="4.3" fill="none" stroke="#fff" stroke-width="1.2"/><path d="M3.2 3c.5 2 1.6 3.2 3.6 3.8" stroke="#fff" stroke-width="1.4" fill="none"/></svg>
        520-381-7459
      </div>
      <div class="line">
        <svg viewBox="0 0 10 10"><circle cx="5" cy="5" r="4.3" fill="none" stroke="#fff" stroke-width="1.2"/><path d="M3.2 3c.5 2 1.6 3.2 3.6 3.8" stroke="#fff" stroke-width="1.4" fill="none"/></svg>
        866-381-7459
      </div>
      <div class="line">
        <svg viewBox="0 0 10 10"><rect x="0.5" y="2" width="9" height="6.5" fill="#fff"/><path d="M0.5 2l4.5 3.5L9.5 2" stroke="#5b5c5e" stroke-width="1" fill="none"/></svg>
        mark@trelvanmedia.example
      </div>
      <div class="line">
        <svg viewBox="0 0 10 10"><circle cx="5" cy="5" r="4.3" fill="none" stroke="#fff" stroke-width="1.1"/><ellipse cx="5" cy="5" rx="1.8" ry="4.3" fill="none" stroke="#fff" stroke-width="0.9"/><path d="M0.7 5h8.6" stroke="#fff" stroke-width="0.9"/></svg>
        www.trelvanmedia.example
      </div>
    </div>
  </div>
</section>

<section class="card card--back">
  <svg class="back-mark" viewBox="0 0 220 170" aria-hidden="true">
    <circle cx="110" cy="85" r="80" fill="var(--slate-faint)"/>
  </svg>
  <div class="back-name">trelvan</div>
  <div class="services">
    <h2>Our Services</h2>
    <ul>
      <li>Web Design</li>
      <li>Internet Marketing</li>
      <li>Website Management</li>
    </ul>
  </div>
</section>

</body>
</html>
```